How likely are people to engage in social distancing? We need a good illustration to show the data!

We surveyed U.S. adults March 20th - 24th, 2020 and asked how likely they were to engage in social distancing (and other COVID-19 related health behaviors). What did the survey find? Basically, most people intend to engage in social distancing behaviors (e.g., avoiding large crowds) and other behaviors that reduce the spread of COVID-19 (e.g., washing hands at least 20 seconds). When most people intend to engage in a behavior, then public health professionals try to leverage that to move more people to act.
Now we need innovative and professional images that attempt to communicate one or all of these findings. The specific findings are nicely summarized in the attached document. For example, 82% of participants intend to engage in social distancing.
What sort of visual are we looking for? Our preference is for an original illustration (or set of illustrations). Our preference is for (creative and powerful illustrations, but we are also open to the creative and well-executed infographics.
We need these images fast . We will award monetary prizes to the 3 best designs. If we like more than that, then we might purchase more (e.g., in past contests, we have purchased as many as 30 designs).
What we will need:
(1) The illustrations must be original and we will need the photoshop and/or illustrator files for all artwork.
(2) You can illustrate all of the findings or just one of them. We need creative approaches that do a lucid job of bringing the data to life. Most people intend to engage in these behaviors. How to communicate that? Republicans and Democrats do not differ in their intentions; how to communicate that?
(3) The illustration should say, somewhere: "Based on a survey of 400 U.S. adults conducted March 20 - 24th, 2020."

U.S. Adults

• Original illustrations based on the findings of the survey (see attached document).

```html
<!DOCTYPE html>
<html lang="en">
<head>
<meta charset="utf-8">
<title>Social Distancing Intentions</title>
<link href="https://fonts.googleapis.com/css2?family=Roboto:wght@400&family=Roboto+Condensed:wght@400;700&display=swap" rel="stylesheet">
<style>
  :root{
    --green:#8fca6a;
    --red:#d51f44;
    --blue:#3f85c7;
    --bar-grey:#bcbdc0;
    --icon-grey:#6d6e71;
    --ink:#231f20;
    --frame:#d0d0d0;
    --white:#ffffff;
  }
  *{margin:0;padding:0;box-sizing:border-box}
  html,body{width:760px;height:1200px;overflow:hidden;background:var(--white)}
  .canvas{position:relative;width:760px;height:1200px;border:1px solid var(--frame);font-family:"Roboto Condensed",sans-serif;color:var(--ink)}
  .title{position:absolute;top:32px;left:0;width:100%;text-align:center;font-family:"Roboto",sans-serif;font-size:22px;line-height:30px;font-weight:400}
  .behaviors{position:absolute;top:128px;left:30px;width:700px;display:flex;justify-content:space-between}
  .behavior{width:76px;display:flex;flex-direction:column;align-items:center}
  .tab{width:76px;height:61px;background:var(--green);clip-path:polygon(0 0,100% 0,100% 70%,50% 100%,0 70%);color:var(--white);font-weight:700;font-size:21px;text-align:center;padding-top:14px}
  .icon{width:46px;height:46px;margin-top:9px;border-radius:50%;background:var(--icon-grey);opacity:.85}
  .label{margin-top:14px;width:96px;text-align:center;font-size:12px;line-height:14px;font-weight:700;color:var(--icon-grey)}
  .summary{position:absolute;top:325px;left:30px;width:700px;height:31px;background:var(--green);color:var(--white);font-weight:700;font-size:22px;display:flex;align-items:center;justify-content:center;gap:10px}
  .summary svg{width:20px;height:20px}
  .compare-head{position:absolute;top:400px;left:0;width:100%;text-align:center;font-weight:700;font-size:31px;line-height:42px}
  .compare-head .rep{color:var(--red)}
  .compare-head .dem{color:var(--blue)}
  .shield{position:absolute;top:390px;width:56px;height:63px}
  .shield.left{left:43px}
  .shield.right{left:668px}
  .rows{position:absolute;top:479px;left:37px;width:682px}
  .row{display:flex;justify-content:space-between;height:23px;margin-bottom:7.6px}
  .bar{position:relative;width:333px;height:23px;background:var(--bar-grey);overflow:hidden}
  .bar .fill{position:absolute;top:0;height:100%}
  .bar.rep .fill{left:0;background:var(--red)}
  .bar.dem .fill{right:0;background:var(--blue)}
  .bar .name{position:absolute;left:4px;top:0;line-height:23px;font-size:14px;font-weight:700;color:var(--white);white-space:nowrap}
  .bar .pct{position:absolute;top:0;line-height:23px;font-size:19px;font-weight:700;color:var(--white)}
  .bar.rep .pct{right:2px}
  .bar.dem .pct{left:3px}
  .figure{position:absolute;top:736px;height:411px;border-radius:80px 80px 0 0}
  .figure.rep{left:90px;width:160px;background:var(--red)}
  .figure.dem{left:510px;width:155px;background:var(--blue)}
  .verdict{position:absolute;top:862px;left:0;width:100%;text-align:center;font-weight:700;font-size:28px;line-height:34px}
  .verdict .r{color:var(--red)}
  .verdict .b{color:var(--blue)}
  .source{position:absolute;top:1166px;left:0;width:100%;text-align:center;font-family:"Roboto",sans-serif;font-size:15px}
</style>
</head>
<body>
<div class="canvas">
  <h1 class="title">Percent of Americans intending to engage in social distancing<br>and perform these behaviors to slow the spread of coronavirus</h1>

  <div class="behaviors">
    <div class="behavior"><div class="tab">82%</div><div class="icon" role="img" aria-label="Icon of two people apart"></div><div class="label">Engage<br>In Social<br>Distancing</div></div>
    <div class="behavior"><div class="tab">63%</div><div class="icon" role="img" aria-label="House icon"></div><div class="label">Work<br>From<br>Home</div></div>
    <div class="behavior"><div class="tab">85%</div><div class="icon" role="img" aria-label="Crossed-out crowd icon"></div><div class="label">Avoid<br>Large<br>Gatherings</div></div>
    <div class="behavior"><div class="tab">81%</div><div class="icon" role="img" aria-label="Calendar icon with cancelled day"></div><div class="label">Cancel<br>Social<br>Activities</div></div>
    <div class="behavior"><div class="tab">85%</div><div class="icon" role="img" aria-label="Two people with distance arrow"></div><div class="label">Put Distance<br>Between Yourself<br>And Other<br>People</div></div>
    <div class="behavior"><div class="tab">87%</div><div class="icon" role="img" aria-label="Hand washing icon"></div><div class="label">Wash<br>hands<br>at least 20</div></div>
    <div class="behavior"><div class="tab">85%</div><div class="icon" role="img" aria-label="Hand sanitizer bottle icon"></div><div class="label">Use<br>hand<br>sanitizer</div></div>
    <div class="behavior"><div class="tab">81%</div><div class="icon" role="img" aria-label="Crossed-out face touching icon"></div><div class="label">Avoid<br>touching<br>your eyes, nose</div></div>
  </div>

  <div class="summary">
    <svg viewBox="0 0 20 20"><path d="M2 10 L8 16 L18 4" fill="none" stroke="#fff" stroke-width="3.5"/></svg>
    <span>Most people intend to engage in these behaviors.</span>
  </div>

  <svg class="shield left" viewBox="0 0 56 63"><path d="M28 2 C38 8 48 8 54 6 C56 34 46 52 28 61 C10 52 0 34 2 6 C8 8 18 8 28 2Z" fill="var(--red)"/><path d="M28 10 C35 14 42 15 46 14 C46 34 39 46 28 52 C17 46 10 34 10 14 C14 15 21 14 28 10Z" fill="none" stroke="#fff" stroke-width="2.5"/></svg>
  <h2 class="compare-head">Comparing <span class="rep">Republicans</span> and <span class="dem">Democrats</span></h2>
  <svg class="shield right" viewBox="0 0 56 63"><path d="M28 2 C38 8 48 8 54 6 C56 34 46 52 28 61 C10 52 0 34 2 6 C8 8 18 8 28 2Z" fill="var(--blue)"/><path d="M28 10 C35 14 42 15 46 14 C46 34 39 46 28 52 C17 46 10 34 10 14 C14 15 21 14 28 10Z" fill="none" stroke="#fff" stroke-width="2.5"/></svg>

  <div class="rows">
    <div class="row"><div class="bar rep"><div class="fill" style="width:82%"></div><span class="name">Engage In Social Distancing</span><span class="pct">82%</span></div><div class="bar dem"><div class="fill" style="width:81%"></div><span class="pct">81%</span></div></div>
    <div class="row"><div class="bar rep"><div class="fill" style="width:60%"></div><span class="name">Work From Home</span><span class="pct">60%</span></div><div class="bar dem"><div class="fill" style="width:65%"></div><span class="pct">65%</span></div></div>
    <div class="row"><div class="bar rep"><div class="fill" style="width:85%"></div><span class="name">Avoid Large Gatherings</span><span class="pct">85%</span></div><div class="bar dem"><div class="fill" style="width:84%"></div><span class="pct">84%</span></div></div>
    <div class="row"><div class="bar rep"><div class="fill" style="width:82%"></div><span class="name">Cancel Social Activities</span><span class="pct">82%</span></div><div class="bar dem"><div class="fill" style="width:80%"></div><span class="pct">80%</span></div></div>
    <div class="row"><div class="bar rep"><div class="fill" style="width:84%"></div><span class="name">Put Distance Between Yourself And Other People</span><span class="pct">84%</span></div><div class="bar dem"><div class="fill" style="width:87%"></div><span class="pct">87%</span></div></div>
    <div class="row"><div class="bar rep"><div class="fill" style="width:87%"></div><span class="name">Wash Hands At Least 20 Seconds</span><span class="pct">87%</span></div><div class="bar dem"><div class="fill" style="width:88%"></div><span class="pct">88%</span></div></div>
    <div class="row"><div class="bar rep"><div class="fill" style="width:87%"></div><span class="name">Use Hand Sanitizer</span><span class="pct">87%</span></div><div class="bar dem"><div class="fill" style="width:84%"></div><span class="pct">84%</span></div></div>
    <div class="row"><div class="bar rep"><div class="fill" style="width:80%"></div><span class="name">Avoid Touching Your Eyes, Nose, And Mouth</span><span class="pct">80%</span></div><div class="bar dem"><div class="fill" style="width:82%"></div><span class="pct">82%</span></div></div>
  </div>

  <div class="figure rep" role="img" aria-label="Red silhouette of a person reaching out to shake hands"></div>
  <div class="figure dem" role="img" aria-label="Blue silhouette of a person shaking hands"></div>
  <p class="verdict"><span class="r">No big differences.</span><br><span class="b">Basically the same<br>patterns.</span></p>

  <p class="source">Based on a survey of 400 U.S. adults conducted March 20 - 24th, 2020.</p>
</div>
</body>
</html>
```